Trendy, rustic, patriotic Facebook Design!

Would like something to catch people's eye! Must include our logo and phone number. 318-507-4429. Dogs in the project are a must. Bold pricing, location, etc to catch peoples eyes is a plus.

Target Market(s)

Dog owners

Font styles to use
Serif
Sans Serif

Colors
1f66ae
ec1f27
ffffff

Requirements
Must have
• Dogs, company logo, business phone 318-507-4429 and website www.brindlepawco.com
Nice to have
• Something that is rustic, trendy!
Should not have
• Cartoons.

```html
<!DOCTYPE html>
<html lang="en">
<head>
<meta charset="utf-8">
<title>Brindle Paw Co — Cover</title>
<link rel="stylesheet" href="https://fonts.googleapis.com/css2?family=Montserrat:wght@700;800&family=Nunito+Sans:wght@400;800&display=swap">
<style>
  :root {
    --page-bg: #e9ebee;
    --navy: #0c2b5e;
    --crimson: #b01c35;
    --white: #ffffff;
    --fur-dark: #1d120c;
    --fur-mid: #3a2216;
    --fur-tan: #8a4a1e;
  }
  * { box-sizing: border-box; margin: 0; padding: 0; }
  html, body { width: 1200px; height: 869px; overflow: hidden; background: var(--page-bg); }
  .cover {
    position: absolute; left: 0; top: 206px;
    width: 1200px; height: 456px;
    background: var(--navy); overflow: hidden;
    color: var(--white);
    font-family: "Nunito Sans", Arial, sans-serif;
  }
  .cover__diagonal { position: absolute; inset: 0; }
  .cover__dog-photo {
    position: absolute; left: 790px; top: 0; width: 410px; height: 456px;
    background: linear-gradient(165deg, var(--fur-mid) 0%, var(--fur-dark) 45%, var(--fur-dark) 62%, var(--fur-tan) 100%);
  }
  .brand {
    position: absolute; left: 30px; top: 72px; width: 164px;
    display: flex; flex-direction: column; align-items: center; gap: 10px;
  }
  .brand__mark { width: 62px; height: 62px; border-radius: 50%; border: 3px solid var(--white); }
  .brand__name {
    font-family: "Montserrat", Arial, sans-serif; font-weight: 800;
    font-size: 15px; letter-spacing: .4px; white-space: nowrap;
    color: var(--white);
  }
  .headline {
    position: absolute; left: 199px; top: 60px;
    font-family: "Montserrat", Arial, sans-serif; font-weight: 800;
    font-size: 41px; line-height: 40px; text-transform: uppercase;
  }
  .service-area {
    position: absolute; left: 199px; top: 164px; width: 340px;
    font-size: 20px; line-height: 26px;
  }
  .service-area strong { font-weight: 800; }
  .guarantee-badge {
    position: absolute; left: 43px; top: 270px; width: 130px; height: 130px;
    border-radius: 50%; border: 3px solid var(--white);
  }
  .contact { position: absolute; left: 198px; top: 286px; list-style: none; font-size: 16px; line-height: 20px; }
  .contact li { display: flex; align-items: flex-start; gap: 8px; margin-bottom: 7px; }
  .contact svg { flex: none; margin-top: 2px; }
</style>
</head>
<body>
  <section class="cover">
    <svg class="cover__diagonal" width="1200" height="456" viewBox="0 0 1200 456" aria-hidden="true">
      <polygon points="828,0 1200,0 1200,456 372,456" fill="var(--crimson)"/>
    </svg>
    <div class="cover__dog-photo" role="img" aria-label="Photo of a black and tan Doberman in profile wearing a leather collar, tongue out"></div>

    <div class="brand">
      <div class="brand__mark"></div>
      <div class="brand__name">BRINDLE PAW CO</div>
    </div>

    <h1 class="headline">World-Renowned<br>Dog Training</h1>
    <p class="service-area">Serving <strong>Maryland</strong>, District of Columbia, and Northern Virginia</p>

    <div class="guarantee-badge"></div>

    <ul class="contact">
      <li>
        <svg width="14" height="14" viewBox="0 0 24 24"><path fill="#fff" d="M6.6 10.8a15 15 0 0 0 6.6 6.6l2.2-2.2c.3-.3.7-.4 1-.2 1.1.4 2.3.6 3.6.6.6 0 1 .4 1 1V20c0 .6-.4 1-1 1C10.6 21 3 13.4 3 4c0-.6.4-1 1-1h3.5c.6 0 1 .4 1 1 0 1.3.2 2.5.6 3.6.1.3 0 .7-.2 1z"/></svg>
        <span>(318) 507-4429</span>
      </li>
      <li>
        <svg width="14" height="14" viewBox="0 0 24 24"><circle cx="12" cy="12" r="9" fill="none" stroke="#fff" stroke-width="2"/><path d="M3 12h18M12 3c3 3 3 15 0 18M12 3c-3 3-3 15 0 18" fill="none" stroke="#fff" stroke-width="1.6"/></svg>
        <span>www.brindlepawco.com</span>
      </li>
      <li>
        <svg width="14" height="16" viewBox="0 0 24 28"><path fill="#fff" d="M12 0a9 9 0 0 0-9 9c0 7 9 19 9 19s9-12 9-19a9 9 0 0 0-9-9zm0 13a4 4 0 1 1 0-8 4 4 0 0 1 0 8z"/></svg>
        <span>418 Cedar Hollow Road<br>Millbrook MD 21044</span>
      </li>
    </ul>
  </section>
</body>
</html>
```